Online Training company needs a new website design (Wordpress)

We are looking for a new design for our website (run on WordPress). We currently have two websites (quizbrightly.com) and (velmoracademy.com) and are trying to combine them into a single design.

The site should contain the following sections (Start Here, courses, labs, practice exams, exam vouchers, books, articles, about us).

Start Here - With so many options on our site, we think it would be a good idea to have this page that will allow us to give students an overview of our different products/services and where to start when they first find out about our company.

Courses - These are our online video courses (products), currently hosted at velmoracademy.com. Each course has its own "product page".

Labs - These are online lab environments that a student can purchase. The layout for these would be similar to a course, but the purchase option will be different (our web developer will code all the back end stuff to make it work).

Practice Exams - This will allow students to take practice questions to study for their exams.

Exam Vouchers - Students can purchase their exam vouchers here at a discounted price for their certification exams.

Books - Will link to a page that displays our books that are available on Brixly. (Examples of the covers are attached so you can see our current designs.)

Articles - This will be our "blog" area for us to post articles each week.

About Us - A short about us page describing our company.

***
As for the design of the page itself, we like the current color scheme at velmoracademy.com, but the layout isn't working well. It was fine when we just had video courses, but as we have added new products it is becoming more and more cumbersome.

I have been looking for inspiration around the web, and saw quietharvestplan.com as a good example of trying to provide focus to new users, while breaking out various parts of a business that contains 4-6 different product lines/topics. Another example of a site we like is lessonlanternhub.com.

That said, we aren't looking to simply copy either site, and are completely open to recommendations and designs you may have.

Thank you and we look forward to working with you!

```html
<!DOCTYPE html>
<html lang="en">
<head>
<meta charset="utf-8">
<title>Velmor Academy</title>
<link href="https://fonts.googleapis.com/css2?family=Lato:wght@400;700;900&display=swap" rel="stylesheet">
<style>
:root{
  --ink:#222226;
  --muted:#6d6d74;
  --blue:#2e5796;
  --blue-deep:#264b84;
  --purple:#5a3a8e;
  --red:#d8332b;
  --night:#1e1e22;
  --strip:#2b2b2f;
  --tile:#3a3a3f;
  --chip:#e4e4e8;
  --paper:#ffffff;
  --mist:#f4f4f6;
  --line:#e2e2e6;
}
*{box-sizing:border-box;margin:0;padding:0}
html,body{width:1200px;height:4876px;overflow:hidden}
body{font-family:'Lato',Arial,sans-serif;color:var(--ink);background:var(--paper);position:relative}
.abs{position:absolute}
.photo{background:linear-gradient(135deg,#d9d4cc,#b7aea3 55%,#8c8680)}
.btn{display:inline-block;background:var(--blue);color:#fff;font-size:12px;font-weight:700;letter-spacing:.5px;padding:11px 20px;text-transform:uppercase}
.btn::after{content:" ›"}

/* header */
.header{left:0;top:0;width:1200px;height:72px;background:rgba(20,20,24,.92);z-index:3}
.brand{left:100px;top:22px;display:flex;align-items:center;gap:10px;color:#fff;font-weight:900;font-size:22px;letter-spacing:1px}
.brand-dot{width:24px;height:24px;border-radius:50%;background:#fff}
.nav{right:90px;top:0;display:flex;height:72px}
.nav a{color:#fff;font-size:12px;font-weight:700;text-decoration:none;padding:0 12px;line-height:72px;text-transform:uppercase}
.nav a.active{background:var(--blue)}

/* hero */
.hero{left:0;top:0;width:1200px;height:740px;background:linear-gradient(90deg,#5b5a5e 0%,#9c958d 35%,#d8d2c8 60%,#c3b8aa 100%)}
.hero-copy{left:100px;top:270px;width:520px;color:#fff}
.hero-copy h1{font-size:40px;font-weight:900;letter-spacing:1px;margin-bottom:14px;white-space:nowrap}
.hero-copy p{font-size:15px;line-height:1.5;margin-bottom:22px;width:380px}

/* partner strip */
.badges{left:0;top:740px;width:1200px;height:148px;background:var(--strip);display:flex;justify-content:space-between;align-items:center;padding:0 150px}
.badge{width:120px;height:92px;background:var(--tile);display:flex;align-items:center;justify-content:center}
.badge span{width:80px;height:60px;border-radius:4px;background:var(--chip)}

/* section scaffolding */
.side-label{left:10px;width:60px;display:flex;flex-direction:column;align-items:center}
.side-label b{writing-mode:vertical-rl;transform:rotate(180deg);font-size:14px;font-weight:700;letter-spacing:2px;color:#55555b;text-transform:uppercase}
.side-label i{display:block;width:2px;height:30px;background:#55555b;margin-top:10px}
.side-label.light b{color:#fff}.side-label.light i{background:#fff}
.section-title{left:0;width:1200px;text-align:center;font-size:32px;font-weight:900;text-transform:uppercase;letter-spacing:.5px}
.section-title::after{content:"";display:block;width:50px;height:3px;background:var(--blue);margin:12px auto 0}

/* product cards */
.cards{left:100px;width:1000px;display:flex;justify-content:space-between}
.card{width:300px;height:310px;position:relative;overflow:hidden}
.card .photo{position:absolute;inset:0}
.card-body{position:absolute;left:0;right:0;bottom:0;height:120px;background:rgba(24,24,30,.86);color:#fff;padding:18px 18px}
.card-body h3{font-size:17px;font-weight:700;margin-bottom:8px}
.card-body p{font-size:12px;line-height:1.5;color:#d6d6da}
.card-body.violet{background:rgba(72,44,120,.9)}

/* practice exams */
.practice{left:0;top:1932px;width:1200px;height:308px;background:var(--blue);color:#fff;text-align:center}
.practice h2{font-size:32px;font-weight:900;margin-top:70px;letter-spacing:.5px}
.practice p{width:700px;margin:14px auto 26px;font-size:13px;line-height:1.6;color:#dfe6f2}
.form{display:flex;justify-content:center;gap:16px}
.field{width:240px;height:42px;background:#fff;color:#8a8a90;font-size:13px;text-align:left;padding:13px 14px}
.cta-red{background:var(--red);color:#fff;font-size:12px;font-weight:700;height:42px;padding:14px 22px;text-transform:uppercase}

/* vouchers */
.voucher-sub{left:0;top:2432px;width:1200px;text-align:center;font-size:14px;color:var(--muted)}
.vouchers{left:0;top:2495px;width:1200px;display:flex;justify-content:center;align-items:flex-end}
.voucher{width:260px;height:270px;background:#fff;border:1px solid var(--line);text-align:center;padding:40px 26px}
.voucher h3{font-size:26px;font-weight:900;line-height:1.25}
.voucher hr{border:0;border-top:1px solid var(--line);margin:22px 0}
.voucher p{font-size:12px;line-height:1.6;color:var(--muted)}
.voucher.best{width:300px;height:300px;background:var(--purple);border:0;color:#fff;padding:0 28px}
.voucher.best .flag{background:#47297a;margin:0 -28px 26px;padding:10px 0;font-size:13px;font-weight:700}
.voucher.best p{color:#e3daf0}
.voucher.best hr{border-color:#7b5fae}

/* books */
.books{left:0;top:2900px;width:1200px;height:360px;background:var(--night);color:#fff}
.books-copy{left:100px;top:70px;width:430px}
.books-copy h2{font-size:32px;font-weight:900;margin-bottom:18px}
.books-copy p{font-size:13px;line-height:1.7;color:#c8c8cd;margin-bottom:26px}
.cover{top:30px;width:210px;height:300px}
.cover.one{left:620px;background:linear-gradient(180deg,#e9e9ec 0%,#e9e9ec 40%,#3c2a6b 40%,#2d2156 100%)}
.cover.two{left:880px;background:linear-gradient(180deg,#e9e9ec 0%,#e9e9ec 40%,#1f5d86 40%,#17496c 100%)}

/* articles */
.article{width:300px}
.article .photo{height:170px}
.article h3{font-size:17px;font-weight:700;margin:18px 0 8px}
.meta{font-size:11px;color:#8a8a90;display:flex;gap:16px;margin-bottom:12px}
.meta span::before{content:"";display:inline-block;width:8px;height:8px;background:var(--blue);margin-right:6px;vertical-align:middle}
.article p{font-size:12px;line-height:1.6;color:var(--muted);margin-bottom:16px}
.btn-outline{display:inline-block;border:1px solid #bfbfc5;color:var(--ink);font-size:11px;font-weight:700;padding:8px 14px;text-transform:uppercase}
.btn-outline::after{content:" ›"}

/* about */
.about-copy{left:100px;top:4090px;width:480px}
.about-copy h2{font-size:32px;font-weight:900;margin-bottom:18px}
.about-copy p{font-size:13px;line-height:1.7;color:var(--muted);margin-bottom:26px}
.about-media{left:665px;top:4070px;width:420px;height:300px}

/* footer */
.footer{left:0;top:4490px;width:1200px;height:386px;background:var(--night);color:#fff}
.join{left:100px;top:40px;font-size:24px;font-weight:900;line-height:1.3;text-transform:uppercase}
.subscribe{left:615px;top:55px;display:flex}
.subscribe .field{width:340px;height:44px}
.subscribe .go{background:var(--blue);color:#fff;font-size:12px;font-weight:700;padding:15px 22px;text-transform:uppercase}
.rule{left:100px;top:150px;width:1000px;height:1px;background:#3d3d44}
.socials{left:0;top:184px;width:1200px;display:flex;justify-content:center;gap:18px}
.socials span{width:40px;height:40px;border-radius:50%;border:2px solid #cfcfd4}
.foot-links{left:0;top:262px;width:1200px;display:flex;justify-content:center;gap:22px;font-size:13px}
.copyright{left:0;top:300px;width:1200px;text-align:center;font-size:12px;color:#a9a9b0}
</style>
</head>
<body>

<div class="abs hero" role="img" aria-label="Student with headphones writing notes at a laptop in a bright study room"></div>
<header class="abs header">
  <div class="abs brand"><span class="brand-dot"></span>VELMOR ACADEMY</div>
  <nav class="abs nav">
    <a class="active">Home</a><a>Courses</a><a>Labs</a><a>Practice Exams</a><a>Exam Vouchers</a><a>Books</a><a>Articles</a><a>About</a>
  </nav>
</header>
<div class="abs hero-copy">
  <h1>VELMOR ACADEMY</h1>
  <p>Train for your next certification with focused video courses and labs.</p>
  <span class="btn">Read More</span>
</div>

<div class="abs badges">
  <div class="badge"><span></span></div>
  <div class="badge"><span></span></div>
  <div class="badge"><span></span></div>
  <div class="badge"><span></span></div>
</div>

<div class="abs side-label" style="top:930px"><b>Our Courses</b><i></i></div>
<h2 class="abs section-title" style="top:990px">Our Courses</h2>
<div class="abs cards" style="top:1075px">
  <div class="card"><div class="photo" role="img" aria-label="Laptop showing an online study screen"></div>
    <div class="card-body"><h3>Full Access to All Our Courses</h3><p>One plan unlocks every video course, quiz and update we publish for you.</p></div></div>
  <div class="card"><div class="photo" role="img" aria-label="Learner watching a video lesson at a desk"></div>
    <div class="card-body"><h3>SERVA Foundation</h3><p>Purchase our discounted SERVA Foundation video course directly from us.</p></div></div>
  <div class="card"><div class="photo" role="img" aria-label="Student studying with a laptop and notebook"></div>
    <div class="card-body"><h3>PROJEX2 Foundation</h3><p>Purchase our discounted PROJEX2 Foundation video course directly from us.</p></div></div>
</div>

<div class="abs side-label" style="top:1450px"><b>Our Labs</b><i></i></div>
<h2 class="abs section-title" style="top:1440px">Our Labs</h2>
<div class="abs cards" style="top:1525px">
  <div class="card"><div class="photo" role="img" aria-label="Hands holding a tablet with a lab dashboard"></div>
    <div class="card-body violet"><h3>Certix Analyst+ Practice Labs</h3><p>Work through live lab tasks in a safe online environment.</p></div></div>
  <div class="card"><div class="photo" role="img" aria-label="Person working on a laptop in a lab session"></div>
    <div class="card-body"><h3>Certix Probe+ Practice Labs</h3><p>Hands-on testing scenarios built to match the real exam.</p></div></div>
  <div class="card"><div class="photo" role="img" aria-label="Learner on a video call with an instructor"></div>
    <div class="card-body"><h3>Certix Guard+ Practice Labs</h3><p>Practice core security skills with guided lab exercises.</p></div></div>
</div>

<section class="abs practice">
  <h2>PRACTICE EXAMS</h2>
  <p>Test yourself with realistic practice questions written by our instructors. Enter your details below and we will send a free set of questions straight to your inbox.</p>
  <div class="form"><div class="field">Full Name</div><div class="field">Email Address</div><div class="cta-red">Get Practice Questions</div></div>
</section>
<div class="abs side-label light" style="top:1960px"><b>Practice Exams</b><i></i></div>

<div class="abs side-label" style="top:2420px"><b>Exam Vouchers</b><i></i></div>
<h2 class="abs section-title" style="top:2350px">Exam Vouchers</h2>
<p class="abs voucher-sub">Choose the Velmor Academy voucher bundle that best fits your needs.</p>
<div class="abs vouchers">
  <div class="voucher"><h3>Buy 5 Exams<br>Save 15%</h3><hr><p>Bundle five exam vouchers and save on every certification.</p></div>
  <div class="voucher best"><div class="flag">Best Deal For You</div><h3>Buy 10 Exams<br>Save 15%</h3><hr><p>Our biggest bundle for teams and learners planning a full certification path this year.</p></div>
  <div class="voucher"><h3>Special Offer<br>2nd Shot</h3><hr><p>Get a free retake voucher if your first attempt falls short.</p></div>
</div>

<section class="abs books">
  <div class="abs books-copy">
    <h2>OUR BOOKS</h2>
    <p>Our study guides condense each exam into clear, focused chapters with review questions and memory aids, so you can prepare quickly and walk into test day with confidence.</p>
    <span class="btn">Buy on Brixly</span>
  </div>
  <div class="abs cover one" role="img" aria-label="Book cover: PROJEX2 Foundation study guide by Marek Holloway"></div>
  <div class="abs cover two" role="img" aria-label="Book cover: SERVA Foundation study guide by Marek Holloway"></div>
</section>
<div class="abs side-label light" style="top:2950px"><b>Our Books</b><i></i></div>

<div class="abs side-label" style="top:3480px"><b>Latest Articles</b><i></i></div>
<h2 class="abs section-title" style="top:3410px">Latest Articles</h2>
<div class="abs cards" style="top:3500px">
  <div class="article"><div class="photo" role="img" aria-label="Hands typing on a laptop at a desk"></div>
    <h3>Role Of Automation In Hiring</h3><div class="meta"><span>Feb 12, 2018</span><span>Velmor Team</span></div>
    <p>Automation now shapes how teams screen candidates and plan training, making certified skills easier to spot early.</p><span class="btn-outline">Read More</span></div>
  <div class="article"><div class="photo" role="img" aria-label="Phone with red app screen beside a notebook"></div>
    <h3>7-Step Process Improvement…</h3><div class="meta"><span>Mar 03, 2018</span><span>Velmor Team</span></div>
    <p>The seven step improvement process is a core part of service management and a common exam topic to review.</p><span class="btn-outline">Read More</span></div>
  <div class="article"><div class="photo" role="img" aria-label="Man working at a laptop in a bright room"></div>
    <h3>Measurements And Metrics</h3><div class="meta"><span>Jan 18, 2018</span><span>Velmor Team</span></div>
    <p>To improve a service you must first measure it. Here is how to pick metrics that actually guide decisions.</p><span class="btn-outline">Read More</span></div>
</div>

<div class="abs side-label" style="top:4100px"><b>About Us</b><i></i></div>
<div class="abs about-copy">
  <h2>ABOUT US</h2>
  <p>Velmor Academy is a certification training company founded by experienced IT instructors. We build practical courses, labs and practice exams that help learners pass on their first try, with instructors holding many industry certifications across security, networking and service management.</p>
  <span class="btn">Read More</span>
</div>
<div class="abs about-media photo" role="img" aria-label="Video still of a student writing notes at a laptop"></div>

<footer class="abs footer">
  <div class="abs join">Want to know about us<br>Join the community</div>
  <div class="abs subscribe"><div class="field">Email Address</div><div class="go">Subscribe</div></div>
  <div class="abs rule"></div>
  <div class="abs socials"><span></span><span></span><span></span><span></span></div>
  <div class="abs foot-links"><span>Home</span><span>Courses</span><span>Labs</span><span>Practice Exams</span><span>Exam Vouchers</span><span>Books</span><span>Articles</span><span>About Us</span></div>
  <div class="abs copyright">Copyright © 2018 Velmor Academy Solutions. All Rights Reserved.</div>
</footer>

</body>
</html>
```